Web Design Project

I need a three page website. I have designed the index.html and the specialevent.html page.

I need someone to finetune the pages for me.

Where I have difficulty is with the following:
I want to add an event table driven by php database.
The administrator of the event will login and create the wording that fits under each colmn. The administrator the submit the form to php database. The database then display in a html.

The Table contains 5 coloums and the rows can vary and can go up to as many as 100.

The table set out events on a program
In the last column of every row I need a submit button to "View and Book" I need to link those buttons with external links/pages.

I use Dreamweaver CS5 and I need to have it in this format in order for me to edit it in the future.

The Table needs to be updated once a year for this program. So ideally if someone has a password to update the certain regions this is what I have in mind.

I have also designed a mockup of the restaurant page. At the top I need.
1) 4 Colapsable panels
a) Restaurants - opening the names of the restaurants
b) Coffee shops and light lunches .... with the names
c) Family
d) Home eateries

From the colapsable panel of each of these I need a anchored link to the description/photos of each...with a BOOK now button I can submit bookings to.

I added a colapsable panel in each restaurants description to keep everything contained.

Please help

• Background must be fixed so that main.div scroll over it

The colours are chosen so please stick to it.

The green for the submit button I short is. #C8D707

I need to edit the pages in Dreamweaver CS5. /Flexilayout2pro

Please ask if you need to know anything. I exactly know what I want.

Kind regards
Pieter Vansloten

The colours are fine.

The wording " karoovistadirect BOOKING agent" should appear right at the top in the white horizon part of the background image.

The specialevent page I described already. I am interested in the editable solution. for this.

I will make up a mockup of the third page and send it later.

Regards

```html
<!DOCTYPE html>
<html lang="en">
<head>
<meta charset="utf-8">
<title>karoovistadirect BOOKING agent</title>
<link rel="stylesheet" href="https://fonts.googleapis.com/css2?family=Ubuntu:wght@700&family=Source+Sans+3:wght@400;600&family=Signika:wght@400;600;700&display=swap">
<style>
:root{
  --lime:#c8d707;
  --lime-dark:#9aab06;
  --lime-text:#94a80a;
  --orange:#f05a1a;
  --sky:#29abe2;
  --ink:#1e1e1e;
  --muted:#5a5a5a;
  --grey-head:#b3b3b3;
  --panel:#ffffff;
  --page:#ececec;
  --dark:#333333;
}
*{box-sizing:border-box;margin:0;padding:0}
html,body{width:972px;height:1200px;overflow:hidden}
body{position:relative;background:linear-gradient(#f5f5f5,var(--page) 60%,#e4e4e4);font-family:"Source Sans 3",sans-serif;color:var(--ink)}
.hero{position:absolute;left:0;top:0;width:972px;height:467px;background:linear-gradient(180deg,#9a9a9a 0%,#6e6e6a 25%,#55554f 55%,#7a7a76 80%,#8c8c88 100%)}
.site-title{position:absolute;top:10px;left:0;width:972px;text-align:center;font-family:"Ubuntu",sans-serif;font-weight:700;font-size:39px;letter-spacing:1.5px;color:#f2f2f2;white-space:nowrap}
.site-title .brand{color:var(--lime)}
.main-nav{position:absolute;left:80px;top:64px;width:811px;height:41px;background:linear-gradient(#c8d707,#a2b004);border-radius:3px;display:flex;align-items:center}
.main-nav a{font-family:"Signika",sans-serif;font-weight:600;font-size:13px;color:#3d4400;text-decoration:none;height:41px;line-height:41px;padding:0 20px;border-right:1px solid #8e9a04}
.search{position:absolute;right:6px;top:7px;width:221px;height:28px;background:#fff;border-radius:3px;font-size:12px;color:#888;line-height:28px;padding-left:13px}
.search span{position:absolute;right:5px;top:4px;width:20px;height:20px;background:linear-gradient(#999,#666);border-radius:2px}
.search svg{position:absolute;left:4px;top:4px}
.panel{position:absolute;left:80px;top:401px;width:811px;height:700px;background:var(--panel)}
.panel h1{position:absolute;top:14px;width:100%;text-align:center;font-family:"Signika",sans-serif;font-weight:700;font-size:34px;color:var(--grey-head);letter-spacing:.3px}
.services{position:absolute;left:2px;top:60px;width:807px;height:208px;background:linear-gradient(#fff,#f6f6f6);display:flex}
.service{flex:1;text-align:center;border-right:1px solid #e6e6e6;padding-top:8px}
.service:last-child{border-right:none}
.service h2{font-family:"Signika",sans-serif;font-weight:400;font-size:23px;margin-top:4px}
.service h2 b{font-weight:700;font-size:27px}
.stay h2{color:var(--orange)} .play h2{color:var(--lime-dark)} .eat h2{color:var(--sky)}
.service .lead{font-size:15.5px;line-height:20px;margin-top:5px}
.service .note{font-size:12px;line-height:17px;color:var(--muted);margin-top:7px}
.divider{position:absolute;left:20px;top:271px;width:771px;height:10px;background:radial-gradient(ellipse at top,rgba(0,0,0,.12),transparent 70%)}
.events-head{position:absolute;left:13px;top:300px;font-size:19px;font-weight:400;color:var(--ink)}
.next{position:absolute;left:784px;top:305px;width:14px;height:14px}
.card{position:absolute;top:335px;width:251px;height:232px;border:1px solid #ddd;background:linear-gradient(#fff,#f7f7f7)}
.card .photo{position:absolute;left:7px;top:8px;width:236px;height:114px}
.card h3{position:absolute;left:13px;top:134px;font-weight:400;font-size:18px;color:var(--lime-text);white-space:nowrap}
.card h3 span{font-size:15px;color:var(--ink)}
.card .date{position:absolute;left:13px;top:160px;font-size:12px;color:#777}
.card p{position:absolute;left:13px;top:183px;width:228px;font-size:12px;line-height:17px;color:#444}
.contact{position:absolute;left:13px;top:580px;width:786px;height:116px;background:var(--dark);border-radius:2px;color:#fff}
.contact h2{position:absolute;top:13px;width:100%;text-align:center;font-weight:400;font-size:19px;color:var(--lime)}
.contact .line{position:absolute;font-size:15px;white-space:nowrap}
.social{position:absolute;top:59px;width:25px;height:25px;background:#f2f2f2;border-radius:2px}
.footer-links{position:absolute;left:80px;top:1129px;font-size:12px;color:#222}
.footer-links span{margin:0 9px}
.copyright{position:absolute;left:80px;top:1156px;font-size:12px;color:#222;word-spacing:2px}
.newsletter{position:absolute;left:665px;top:1138px;width:221px;height:27px;border:1px solid #ddd;background:#fff;font-size:11px;color:#777;line-height:25px;padding-left:10px}
.newsletter span{position:absolute;right:3px;top:3px;width:19px;height:19px;background:#eee}
.newsletter svg{position:absolute;left:6px;top:4px}
</style>
</head>
<body>
<div class="hero" role="img" aria-label="Black and white photo of a small town with a church steeple and mountains behind"></div>
<div class="site-title"><span class="brand">KAROOVISTADIRECT</span> BOOKING AGENT</div>

<nav class="main-nav">
  <a>HOME</a><a>ACCOMMODATION</a><a>PLAY</a><a>CONTACT</a>
  <div class="search">Search<span><svg width="12" height="12" viewBox="0 0 12 12"><circle cx="5" cy="5" r="3.5" fill="none" stroke="#fff" stroke-width="1.6"/><path d="M7.5 7.5L11 11" stroke="#fff" stroke-width="1.8"/></svg></span></div>
</nav>

<main class="panel">
  <h1>YOUR BOKING AGENT FOR...</h1>
  <section class="services">
    <div class="service stay">
      <svg width="46" height="42" viewBox="0 0 46 42"><path d="M23 2L2 21h6v19h11V28h8v12h11V21h6z" fill="var(--orange)"/></svg>
      <h2>BOOK <b>STAY</b></h2>
      <p class="lead">Find the perfect accommodation<br>to suit your specific needs.</p>
      <p class="note">Click on bookStay to view and book our<br>properties online NOW!</p>
    </div>
    <div class="service play">
      <svg width="46" height="42" viewBox="0 0 46 42"><circle cx="23" cy="9" r="4" fill="var(--lime-dark)"/><path d="M20 15h6v26h-6z M2 6c6 2 10 8 18 11v4C12 18 7 12 2 6z M44 6c-6 2-10 8-18 11v4c8-3 13-9 18-15z" fill="var(--lime-dark)"/></svg>
      <h2>BOOK <b>PLAY</b></h2>
      <p class="lead">Find the perfect accommodation<br>to suit your specific needs.</p>
      <p class="note">Click on bookStay to view and book our<br>properties online NOW!</p>
    </div>
    <div class="service eat">
      <svg width="46" height="42" viewBox="0 0 46 42"><path d="M13 1h2v10h2V1h2v10h2V1h2v13c0 3-2 4-4 4v23h-4V18c-2 0-4-1-4-4z M28 1c5 0 7 7 7 15h-3v25h-4z" fill="var(--sky)"/></svg>
      <h2>BOOK <b>EAT</b></h2>
      <p class="lead">Find the perfect accommodation<br>to suit your specific needs.</p>
      <p class="note">Click on bookStay to view and book our<br>properties online NOW!</p>
    </div>
  </section>
  <div class="divider"></div>

  <h2 class="events-head">Special Events and Festivals</h2>
  <svg class="next" viewBox="0 0 14 14"><circle cx="7" cy="7" r="7" fill="#c4c4c4"/><path d="M6 4l3 3-3 3" fill="none" stroke="#fff" stroke-width="1.6"/></svg>

  <article class="card" style="left:13px">
    <div class="photo" role="img" aria-label="Market stall with olives, berries and sunflowers" style="background:linear-gradient(135deg,#7a3a22,#b6302e 40%,#6f7a2a 70%,#d9a020)"></div>
    <h3>Olive festival <span>(April 2013)</span></h3>
    <div class="date">August - 29 - 2013</div>
    <p>Aliquam lorem odio, elementum vitae augue at, auctor posuere neque tincidunt.</p>
  </article>
  <article class="card" style="left:280px">
    <div class="photo" role="img" aria-label="Festival crowd in colourful carnival masks" style="background:linear-gradient(135deg,#3f8fd0,#d8c02a 45%,#c83a2a 70%,#b9a030)"></div>
    <h3>Olive festival <span>(April 2013)</span></h3>
    <div class="date">August - 29 - 2013</div>
    <p>Aliquam lorem odio, elementum vitae augue at, auctor posuere neque tincidunt.</p>
  </article>
  <article class="card" style="left:547px">
    <div class="photo" role="img" aria-label="Large group in yellow shirts celebrating in a street" style="background:linear-gradient(135deg,#8a8070,#c9b63a 45%,#6a5d4a 75%,#a09a80)"></div>
    <h3>Olive festival <span>(April 2013)</span></h3>
    <div class="date">August - 29 - 2013</div>
    <p>Aliquam lorem odio, elementum vitae augue at, auctor posuere neque tincidunt.</p>
  </article>

  <section class="contact">
    <h2>Contact us</h2>
    <div class="line" style="left:54px;top:48px">Address : Olyfboom Lane,</div>
    <div class="line" style="left:111px;top:75px">Doringvale</div>
    <div class="line" style="left:314px;top:48px">Phone : 555 014 2020</div>
    <div class="line" style="left:314px;top:75px">Email &nbsp;: info@kvdirect.example</div>
    <div class="line" style="left:573px;top:61px">Follow us on :</div>
    <div class="social" style="left:671px" role="img" aria-label="Social network link"></div>
    <div class="social" style="left:712px" role="img" aria-label="Social network link"></div>
    <div class="social" style="left:752px" role="img" aria-label="Social network link"></div>
  </section>
</main>

<div class="footer-links">Business directory<span>|</span>Relevant Links and Website<span>|</span>Emergency Numbers<span>|</span>Privacy Policy</div>
<div class="copyright">Copyright &copy; 2013 &nbsp;KV Direct. &nbsp;All rights reserved</div>
<div class="newsletter">Enter Email for Newsletter signup<span><svg width="8" height="11" viewBox="0 0 8 11"><path d="M0 0l8 5.5L0 11z" fill="#222"/></svg></span></div>
</body>
</html>
```